Business Card for a Jewellery Brand

Business card for an upscale jewellery brand. Attached is the brand logo and icon and color board. I am looking for two card versions: one for the founder and one is generic. The card should be elegant and convey upscale and premium feel. I am open to both square and rectangle card shapes.

Industry/Entity Type

Jewelry

Contact Information for Business Card

Two cards: (1) Sunela Parvaniya (Founder) (2) General
(1) Sunela Parvaniya card should have Name: Sunela Parvaniya, Title: Founder Email id: sunela@quiremo.com.au. Phone no: +61452913307
(2) Generic card should have Email id: info@quiremo.com.au. Phone no: +61436207518

Requirements
Must have
• Workmark
• ICON
• Phone no
• Email ID
• ABN: 58219740312 (Note: ABN is Business number in Australia)
• Website: www.quiremo.com.au
• Instagram: quiremo_jewellery
• Facebook: @quiremojewellery
Nice to have
• Tagline

```html
<!DOCTYPE html>
<html lang="en">
<head>
<meta charset="utf-8">
<title>Quiremo Business Cards</title>
<link href="https://fonts.googleapis.com/css2?family=Lexend:wght@400&family=Raleway:wght@400;500&display=swap" rel="stylesheet">
<style>
  :root {
    --page: #ffffff;
    --rose: #e4968f;
    --rose-band: #e8aaa6;
    --blush: #fce7e1;
    --marble: #e9dfe4;
    --marble-vein: #dcd0d6;
    --ink-grey: #8c8c8c;
    --card-white: #ffffff;
  }
  * { margin: 0; padding: 0; box-sizing: border-box; }
  html, body {
    width: 1200px;
    height: 738px;
    overflow: hidden;
    background: var(--page);
  }
  .canvas {
    position: relative;
    width: 1200px;
    height: 738px;
    background: var(--page);
  }
  .card {
    position: absolute;
    top: 137px;
    width: 464px;
    height: 464px;
    box-shadow: 7px 9px 14px rgba(0, 0, 0, 0.18);
    overflow: hidden;
  }
  .card--back { left: 93px; background: var(--blush); }
  .card--front { left: 643px; background: var(--card-white); }

  /* back side */
  .marble-field {
    position: absolute;
    left: 0; top: 0;
    width: 464px; height: 317px;
    background: radial-gradient(ellipse at 30% 40%, var(--marble) 0%, var(--marble-vein) 100%);
  }
  .accent-band {
    position: absolute;
    left: 0; top: 317px;
    width: 464px; height: 22px;
    background: var(--rose-band);
  }
  .back-wordmark {
    position: absolute;
    left: 0; top: 132px;
    width: 464px;
    text-align: center;
    font-family: "Raleway", sans-serif;
    font-weight: 500;
    font-size: 40px;
    letter-spacing: 0.14em;
    color: var(--rose);
  }
  .social-list {
    position: absolute;
    left: 121px;
    top: 354px;
    list-style: none;
  }
  .social-item {
    display: flex;
    align-items: center;
    height: 47px;
    font-family: "Raleway", sans-serif;
    font-weight: 400;
    font-size: 24px;
    color: var(--rose);
  }
  .social-marker {
    width: 32px;
    height: 32px;
    margin-right: 14px;
    background: var(--rose);
  }

  /* front side */
  .person-name {
    position: absolute;
    left: 41px; top: 32px;
    font-family: "Lexend", sans-serif;
    font-weight: 400;
    font-size: 26px;
    color: var(--rose);
  }
  .person-role {
    position: absolute;
    left: 41px; top: 64px;
    font-family: "Raleway", sans-serif;
    font-size: 18.5px;
    color: var(--ink-grey);
  }
  .contact-list {
    position: absolute;
    left: 41px; top: 138px;
    list-style: none;
    font-family: "Raleway", sans-serif;
    font-size: 18.5px;
    line-height: 26px;
    color: var(--ink-grey);
  }
  .contact-list .abn { font-size: 15px; }
  .front-wordmark {
    position: absolute;
    right: 41px; top: 368px;
    font-family: "Raleway", sans-serif;
    font-weight: 500;
    font-size: 44px;
    letter-spacing: 0.12em;
    color: var(--rose);
  }
</style>
</head>
<body>
<main class="canvas">
  <section class="card card--back">
    <div class="marble-field" role="img" aria-label="Soft pink marble texture background"></div>
    <div class="back-wordmark">QUIREMO</div>
    <div class="accent-band"></div>
    <ul class="social-list">
      <li class="social-item"><span class="social-marker"></span>quiremo_jewellery</li>
      <li class="social-item"><span class="social-marker"></span>@quiremojewellery</li>
    </ul>
  </section>

  <section class="card card--front">
    <h1 class="person-name">Sunela Parvaniya</h1>
    <p class="person-role">Founder</p>
    <ul class="contact-list">
      <li>+61452913307</li>
      <li>sunela@quiremo.com.au</li>
      <li>www.quiremo.com.au</li>
      <li class="abn">ABN: 58219740312</li>
    </ul>
    <div class="front-wordmark">QUIREMO</div>
  </section>
</main>
</body>
</html>
```